Business Card Design

I need a business card for a new company based in Australia called "MedLinkora".

Its a cloud program for GPs that allows them to search for the specialist they require using a simple user friendly tool.

I would like the colours to match those in the program (the colours in the logo attached).

The final design should reflect the programs clarity, ease of use and professionalism.

Target Market(s)

GPs and other Health Professionals

Industry/Entity Type

Business

Contact Information for Business Card

MedLinkora; The Whole Consultant Index; Marla Voss CEO; 0438215967; marla@medlinkora.example; www.medlinkora.example

Requirements
Must have
• Must have the logo attached; the web address and my name and phone number
Nice to have
• the slogan "The Whole Consultant Index"

```html
<!DOCTYPE html>
<html lang="en">
<head>
<meta charset="utf-8">
<title>MedLinkora Business Card</title>
<link rel="stylesheet" href="https://fonts.googleapis.com/css2?family=Open+Sans:wght@400;600;700&display=swap">
<style>
  :root {
    --brand-blue: #27aee3;
    --ink-grey: #7a7a7a;
    --text-dark: #3a3a3a;
    --card-white: #ffffff;
    --card-black: #050505;
    --backdrop: #e9e6e1;
    --divider: #c9c9c9;
  }
  * { margin: 0; padding: 0; box-sizing: border-box; }
  html, body {
    width: 1200px; height: 829px; overflow: hidden;
    background: var(--backdrop);
    font-family: "Open Sans", Arial, sans-serif;
  }
  .canvas {
    position: relative; width: 1200px; height: 829px;
  }
  .card {
    position: absolute; top: 266px;
    width: 500px; height: 296px;
    border-radius: 4px;
    box-shadow: 0 6px 18px rgba(0,0,0,0.18);
    overflow: hidden;
  }
  .card--front { left: 70px; background: var(--card-white); }
  .card--back { left: 630px; background: var(--card-black); }

  .wordmark {
    font-family: "Open Sans", Arial, sans-serif;
    font-weight: 400;
    color: var(--brand-blue);
    letter-spacing: -1px;
    line-height: 1;
  }
  .slogan {
    color: var(--ink-grey);
    font-weight: 400;
    letter-spacing: 0.3px;
    line-height: 1;
  }

  /* front */
  .card--front .brand { position: absolute; left: 110px; top: 48px; }
  .card--front .wordmark { font-size: 54px; }
  .card--front .slogan { font-size: 15.5px; margin-top: 4px; padding-left: 4px; }

  .person {
    position: absolute; right: 290px; top: 200px; text-align: right;
  }
  .person__name { color: var(--brand-blue); font-weight: 700; font-size: 15px; }
  .person__title { color: var(--ink-grey); font-size: 11px; margin-top: 2px; }

  .rule {
    position: absolute; left: 222px; top: 140px; width: 1px; height: 120px;
    background: var(--divider);
  }
  .contacts {
    position: absolute; left: 236px; top: 146px; list-style: none;
  }
  .contacts li {
    display: flex; align-items: center; gap: 8px;
    font-size: 13px; color: var(--text-dark); height: 22px;
  }
  .contacts svg { width: 14px; height: 14px; flex: none; }

  /* back */
  .card--back .brand {
    position: absolute; left: 0; right: 0; top: 88px; text-align: center;
  }
  .card--back .wordmark { font-size: 60px; }
  .card--back .slogan { font-size: 17px; margin-top: 4px; color: #9a9a9a; }
  .card--back .site {
    position: absolute; left: 0; right: 0; top: 206px; text-align: center;
    color: #f2f2f2; font-size: 17px; letter-spacing: 2px;
  }
</style>
</head>
<body>
<main class="canvas">
  <section class="card card--front" aria-label="Business card front">
    <div class="brand">
      <div class="wordmark">MedLinkora</div>
      <div class="slogan">The Whole Consultant Index</div>
    </div>
    <div class="person">
      <div class="person__name">Marla Voss</div>
      <div class="person__title">CEO</div>
    </div>
    <div class="rule"></div>
    <ul class="contacts">
      <li>
        <svg viewBox="0 0 14 14" aria-hidden="true"><circle cx="7" cy="7" r="7" fill="var(--brand-blue)"/><path d="M4.6 3.6l1.3 1.6-.7.9c.5 1 1.3 1.8 2.3 2.3l.9-.7 1.6 1.3-.8 1.2c-2.7-.4-4.9-2.6-5.3-5.3z" fill="#fff"/></svg>
        0438215967
      </li>
      <li>
        <svg viewBox="0 0 14 14" aria-hidden="true"><circle cx="7" cy="7" r="7" fill="var(--brand-blue)"/><rect x="3.5" y="4.5" width="7" height="5" fill="#fff"/><path d="M3.5 4.5L7 7.3l3.5-2.8" fill="none" stroke="var(--brand-blue)" stroke-width="0.8"/></svg>
        marla@medlinkora.example
      </li>
      <li>
        <svg viewBox="0 0 14 14" aria-hidden="true"><circle cx="7" cy="7" r="7" fill="var(--brand-blue)"/><g fill="none" stroke="#fff" stroke-width="0.8"><circle cx="7" cy="7" r="3.6"/><ellipse cx="7" cy="7" rx="1.5" ry="3.6"/><path d="M3.4 7h7.2"/></g></svg>
        www.medlinkora.example
      </li>
    </ul>
  </section>

  <section class="card card--back" aria-label="Business card back">
    <div class="brand">
      <div class="wordmark">MedLinkora</div>
      <div class="slogan">The Whole Consultant Index</div>
    </div>
    <div class="site">www.medlinkora.example</div>
  </section>
</main>
</body>
</html>
```